Redesign of an existing homepage

This site needs a redesign
https://www.wanderhof-kelbach.de
This page with the accommodation options is important for the customer
https://www.wanderhof-kelbach.de/gastgeber/
Till now there is a new logo. See attachment. That's all I have.
It would make sense to use the colors of the logo in the redesign.
footer.jpg.
I would put this info into the footer. The graphic (Infomaterial) is not needed.
a new menu - links.jpg
This info can be put in a new menu. Therefore the right column is gone and there is more space for the design.
NEW:
Please keep in mind that the Icons are important and shall be displayed under every accommodation

```html
<!DOCTYPE html>
<html lang="de">
<head>
<meta charset="utf-8">
<title>Urlaub im Kelbachtal – Ferienverband Kelbachtal</title>
<link rel="stylesheet" href="https://fonts.googleapis.com/css2?family=Montserrat:wght@500;600;700;800&family=Open+Sans:wght@400;600;700&display=swap">
<style>
:root{
  --green:#79b51c;
  --green-dark:#5f9312;
  --blue:#1f7fc6;
  --blue-dark:#155f9a;
  --blue-light:#d8ecf9;
  --ink:#1f2a36;
  --text:#4a5562;
  --muted:#8a949e;
  --line:#e3e8ee;
  --white:#ffffff;
  --footer-dark:#0f2236;
}
*{box-sizing:border-box;margin:0;padding:0}
html,body{width:1200px;height:4608px;overflow:hidden}
body{font-family:"Open Sans",Arial,sans-serif;color:var(--text);background:var(--white);font-size:14px;line-height:1.5}
h1,h2,h3,h4{font-family:"Montserrat",Arial,sans-serif;color:var(--ink)}
.btn{display:inline-block;font-family:"Montserrat",Arial,sans-serif;font-weight:700;font-size:12px;letter-spacing:.06em;text-transform:uppercase;background:var(--green);color:var(--white);border-radius:20px;padding:9px 22px;text-decoration:none}
.btn-outline{background:var(--white);color:var(--blue);border:2px solid var(--blue)}
.section-title{text-align:center;font-size:30px;font-weight:800;letter-spacing:.02em;text-transform:uppercase}
.section-title::after{content:"";display:block;width:56px;height:4px;border-radius:2px;background:var(--green);margin:14px auto 0}

/* header */
.site-header{height:140px;position:relative;padding:0 152px}
.brand{position:absolute;left:140px;top:26px;display:flex;align-items:center;gap:12px}
.brand-dot{width:46px;height:46px;border-radius:50%;background:var(--green)}
.brand-name{font-family:"Montserrat",Arial,sans-serif;font-weight:800;font-size:17px;line-height:1.15;color:var(--blue);text-transform:uppercase;width:190px}
.contact-bar{position:absolute;right:152px;top:18px;display:flex;gap:34px;font-size:12px}
.contact-item{display:flex;gap:8px;align-items:flex-start;color:var(--ink)}
.contact-item svg{flex:none;margin-top:2px}
.contact-item b{display:block;font-weight:700}
.main-nav{position:absolute;right:152px;top:86px;display:flex;gap:28px;align-items:center;font-family:"Montserrat",Arial,sans-serif;font-weight:600;font-size:14px}
.main-nav a{color:var(--ink);text-decoration:none}
.main-nav a.active{background:var(--blue);color:var(--white);padding:7px 16px;border-radius:18px}

/* hero */
.hero{position:relative;height:540px;background:linear-gradient(180deg,#9fc4dc 0%,#c6d8df 30%,#6f8f6c 55%,#2f6a5e 75%,#1d4a4c 100%);text-align:center;color:var(--white)}
.hero-title{padding-top:88px;font-family:"Montserrat",Arial,sans-serif;font-weight:800;font-size:60px;color:var(--white);line-height:1.1}
.hero-sub{font-family:"Montserrat",Arial,sans-serif;font-weight:600;font-size:34px;margin-top:6px}
.hero .btn{margin-top:28px}
.slider-arrow{position:absolute;top:250px;width:40px;height:40px}
.slider-arrow.prev{left:70px}.slider-arrow.next{right:70px}

/* partners */
.partners{height:100px;display:flex;justify-content:space-between;align-items:center;padding:0 160px}
.partner-badge{width:150px;height:48px;border-radius:6px;background:#e8eef3}
.partner-badge.round{width:56px;height:56px;border-radius:50%;background:#dfeccd}
.partner-badge.wide{width:190px;background:#e1ecf6}

/* hosts */
.hosts{height:820px;position:relative;background:linear-gradient(180deg,#fff 0%,#fff 72%,#eaf4fb 100%)}
.hosts .section-title{padding-top:88px}
.host-list{position:absolute;top:180px;left:152px;right:152px;display:flex;gap:32px}
.host-card{flex:1;background:var(--white);border-radius:10px;box-shadow:0 6px 24px rgba(20,50,80,.14);overflow:hidden;height:450px;position:relative}
.host-card.featured{box-shadow:0 10px 32px rgba(20,80,140,.24)}
.host-photo{height:170px;position:relative}
.host-tag{position:absolute;left:10px;top:10px;background:var(--green);color:var(--white);font-size:10px;font-weight:700;padding:3px 10px;border-radius:10px}
.host-body{padding:16px 18px}
.host-name{font-size:17px;font-weight:700}
.host-address{font-size:11px;color:var(--muted);margin-top:2px}
.host-price{margin-top:12px;color:var(--blue);font-family:"Montserrat",Arial,sans-serif;font-weight:800;font-size:26px}
.host-price small{font-size:11px;font-weight:600;color:var(--muted)}
.host-desc{font-size:12px;margin-top:8px;line-height:1.55}
.host-card .btn{position:absolute;left:18px;bottom:20px;font-size:11px;padding:7px 18px}
.host-arrow{position:absolute;top:430px;width:32px;height:32px}
.host-arrow.prev{left:60px}.host-arrow.next{right:60px}
.hosts-more{position:absolute;top:720px;left:0;right:0;text-align:center}
.skyline{position:absolute;left:0;right:0;bottom:0;height:150px;background:linear-gradient(180deg,rgba(31,127,198,0) 0%,rgba(31,127,198,.10) 100%)}

/* leisure */
.leisure{height:680px;position:relative;background:linear-gradient(180deg,#cfe6f6 0%,#b8dbf2 40%,#8fb7b3 70%,#5f8a6a 100%)}
.leisure .section-title{padding-top:52px}
.leisure-list{position:absolute;top:140px;left:152px;right:152px;display:flex;gap:12px}
.leisure-card{flex:1;background:var(--white);border-radius:8px;overflow:hidden;height:260px;box-shadow:0 4px 16px rgba(0,40,80,.15)}
.leisure-card.highlight{background:var(--green)}
.leisure-photo{height:130px}
.leisure-body{padding:12px 14px}
.leisure-name{font-size:13px;font-weight:800;color:var(--ink)}
.leisure-card.highlight .leisure-name,.leisure-card.highlight .leisure-text{color:var(--white)}
.leisure-text{font-size:11px;margin-top:4px;line-height:1.45}
.leisure-card .btn{margin-top:10px;font-size:9px;padding:4px 12px}
.leisure-card.highlight .btn{background:var(--white);color:var(--green)}
.leisure-all{position:absolute;top:450px;left:0;right:0;text-align:center}
.leisure-all .btn{background:var(--blue)}
.leisure-wave{position:absolute;left:0;bottom:0;width:1200px;height:110px}

/* welcome */
.welcome{height:600px;position:relative;padding:0 152px}
.welcome-text{position:absolute;left:152px;top:20px;width:420px}
.welcome-kicker{font-family:"Montserrat",Arial,sans-serif;font-weight:600;font-size:18px;color:var(--ink);text-transform:uppercase}
.welcome-title{font-size:30px;font-weight:800;line-height:1.15;text-transform:uppercase}
.welcome-title::after{content:"";display:block;width:56px;height:4px;border-radius:2px;background:var(--green);margin:14px 0 18px}
.welcome-lead{font-weight:700;color:var(--ink);font-size:13px}
.welcome-text p{font-size:13px;margin-bottom:12px}
.welcome-photo{position:absolute;left:620px;top:20px;width:428px;height:420px;border-radius:14px;overflow:hidden}
.welcome-photo .photo{width:100%;height:100%;background:linear-gradient(180deg,#5aa0d8 0%,#9cc8e8 35%,#b88c62 55%,#4f7f3c 75%,#3b6a30 100%)}
.welcome-photo svg{position:absolute;left:0;bottom:0}

/* discover */
.discover{height:480px;background:var(--blue-light);position:relative}
.discover .section-title{padding-top:96px;line-height:1.25}
.town-list{position:absolute;top:260px;left:152px;right:152px;display:flex;justify-content:space-between}
.town{width:130px;text-align:center}
.town-photo{width:130px;height:130px;border-radius:50%;border:4px solid var(--white);box-shadow:0 4px 14px rgba(0,50,100,.15)}
.town-name{margin-top:10px;font-family:"Montserrat",Arial,sans-serif;font-weight:600;font-size:13px;color:var(--ink)}

/* directions */
.directions{height:380px;position:relative}
.directions-title{position:absolute;left:152px;top:40px;font-size:22px;font-weight:800;text-transform:uppercase}
.map-area{position:absolute;left:152px;top:90px;width:428px;height:270px;border-radius:6px;background:linear-gradient(135deg,#dfe9d8 0%,#cfe0c6 50%,#e3e6e0 100%)}
.video-area{position:absolute;left:620px;top:90px;width:428px;height:270px;border-radius:6px;background:linear-gradient(180deg,#6fa55a 0%,#4e8a3e 55%,#3c7130 100%)}
.video-area svg{position:absolute;left:184px;top:105px}

/* footer */
.site-footer{height:868px;position:relative;background:linear-gradient(180deg,#a9cbe6 0%,#c9dce6 18%,#6d8c7c 34%,#3f6e5a 46%,#2d6f8c 58%,#1d5c82 100%)}
.footer-panel{position:absolute;left:0;right:0;top:440px;height:368px;background:var(--white)}
.footer-curve{position:absolute;left:0;top:380px;width:1200px;height:62px}
.footer-brand{position:absolute;left:140px;top:490px;display:flex;flex-direction:column;align-items:center;gap:12px;width:220px}
.footer-brand .brand-dot{width:90px;height:90px}
.footer-brand .brand-name{text-align:center;font-size:20px;width:220px}
.footer-cols{position:absolute;left:560px;top:480px;display:flex;gap:60px;font-size:12px}
.footer-col h4{font-size:13px;font-weight:800;text-transform:uppercase;margin-bottom:10px}
.footer-col p,.footer-col li{color:var(--text);line-height:1.6;list-style:none}
.footer-col a{color:var(--blue);text-decoration:underline}
.footer-bottom{position:absolute;left:0;right:0;bottom:0;height:60px;background:var(--footer-dark);color:#c6d2de;font-size:12px;display:flex;justify-content:center;align-items:center;gap:18px}
</style>
</head>
<body>

<header class="site-header">
  <div class="brand"><span class="brand-dot"></span><span class="brand-name">Ferienverband Kelbachtal</span></div>
  <div class="contact-bar">
    <div class="contact-item">
      <svg width="14" height="14" viewBox="0 0 24 24"><circle cx="12" cy="12" r="10" fill="none" stroke="#1f7fc6" stroke-width="2"/><path d="M12 6v6l4 2" stroke="#1f7fc6" stroke-width="2" fill="none"/></svg>
      <div><b>Öffnungszeiten</b>Mo-Fr 9:00 - 17:00 Uhr</div>
    </div>
    <div class="contact-item">
      <svg width="14" height="14" viewBox="0 0 24 24"><rect x="3" y="8" width="18" height="11" rx="2" fill="none" stroke="#1f7fc6" stroke-width="2"/><rect x="7" y="3" width="10" height="6" fill="none" stroke="#1f7fc6" stroke-width="2"/></svg>
      <div><b>Fax</b>01234 / 555 149</div>
    </div>
    <div class="contact-item">
      <svg width="14" height="14" viewBox="0 0 24 24"><path d="M5 3h4l2 5-3 2a12 12 0 0 0 6 6l2-3 5 2v4a2 2 0 0 1-2 2A17 17 0 0 1 3 5a2 2 0 0 1 2-2z" fill="#1f7fc6"/></svg>
      <div><b>Tel</b>01234 / 555 140</div>
    </div>
  </div>
  <nav class="main-nav">
    <a class="active" href="https://www.wanderhof-kelbach.de">Home</a>
    <a href="https://www.wanderhof-kelbach.de/gastgeber/">Gastgeber</a>
    <a href="#">Kelbachtal Freizeit</a>
    <a href="#">Ausflugsziele</a>
    <a href="#">Kunst und Kultur</a>
    <a href="#">Kontakt</a>
  </nav>
</header>

<section class="hero" role="img" aria-label="Bergsee mit Wanderer vor Alpenpanorama im Abendlicht">
  <h1 class="hero-title">Urlaub im Kelbachtal</h1>
  <p class="hero-sub">dem schönsten Fleck Bayerns</p>
  <a class="btn" href="#">Mehr lesen</a>
  <svg class="slider-arrow prev" viewBox="0 0 40 40"><path d="M25 8 13 20l12 12" stroke="#fff" stroke-width="4" fill="none" stroke-linecap="round"/></svg>
  <svg class="slider-arrow next" viewBox="0 0 40 40"><path d="M15 8l12 12-12 12" stroke="#fff" stroke-width="4" fill="none" stroke-linecap="round"/></svg>
</section>

<section class="partners" aria-label="Partner">
  <span class="partner-badge"></span>
  <span class="partner-badge round"></span>
  <span class="partner-badge wide"></span>
  <span class="partner-badge wide"></span>
</section>

<section class="hosts">
  <div class="skyline" role="img" aria-label="Dezente Silhouette von Stadt und Pferd als Hintergrund"></div>
  <h2 class="section-title">Host in the Kelbachtal</h2>
  <svg class="host-arrow prev" viewBox="0 0 32 32"><path d="M20 6 10 16l10 10" stroke="#8a949e" stroke-width="3" fill="none" stroke-linecap="round"/></svg>
  <svg class="host-arrow next" viewBox="0 0 32 32"><path d="M12 6l10 10-10 10" stroke="#8a949e" stroke-width="3" fill="none" stroke-linecap="round"/></svg>
  <div class="host-list">
    <article class="host-card">
      <div class="host-photo" role="img" aria-label="Pension mit Garten und Pergola" style="background:linear-gradient(160deg,#8fbf6a,#5c8a3e 60%,#b68a5c)"><span class="host-tag">Pension</span></div>
      <div class="host-body">
        <h3 class="host-name">Pension Mairhofer</h3>
        <p class="host-address">Wiesengrund 9, 00101 Kelbach</p>
        <p class="host-price"><small>ab</small> € 40.00 <small>pro Person</small></p>
        <p class="host-desc">Ruhige Pension im Grünen mit großem Garten, Terrasse und reichhaltigem Frühstück für Ihren Urlaub.</p>
      </div>
      <a class="btn" href="#">Jetzt buchen</a>
    </article>
    <article class="host-card featured">
      <div class="host-photo" role="img" aria-label="Seehotel aus der Vogelperspektive" style="background:linear-gradient(160deg,#7aa85a,#a77a52 50%,#6f9a4c)"><span class="host-tag">Hotel</span></div>
      <div class="host-body">
        <h3 class="host-name">Seehotel Lindner</h3>
        <p class="host-address">Uferweg 21, 00102 Bad Lindau</p>
        <p class="host-price"><small>ab</small> € 96.00 <small>pro Nacht</small></p>
        <p class="host-desc">Das Seehotel liegt direkt am Ufer, mit eigener Liegewiese und gemütlichen Zimmern mit Seeblick.</p>
      </div>
      <a class="btn" href="#">Jetzt buchen</a>
    </article>
    <article class="host-card">
      <div class="host-photo" role="img" aria-label="Landhaus mit Balkon unter blauem Himmel" style="background:linear-gradient(180deg,#6fb0e8,#d8d2c4 55%,#8a6a4a)"><span class="host-tag">Ferienhaus</span></div>
      <div class="host-body">
        <h3 class="host-name">Landhaus Brunnhuber</h3>
        <p class="host-address">Lindenstraße 17, 00103 Haselried</p>
        <p class="host-price"><small>ab</small> € 38.00 <small>für 2 Personen</small></p>
        <p class="host-desc">Ferienhaus mit Blick ins Grüne, voll ausgestatteter Küche und großem Balkon für die ganze Familie.</p>
      </div>
      <a class="btn" href="#">Jetzt buchen</a>
    </article>
  </div>
  <div class="hosts-more"><a class="btn btn-outline" href="https://www.wanderhof-kelbach.de/gastgeber/">Alle Immobilien ansehen</a></div>
</section>

<section class="leisure">
  <h2 class="section-title">Freizeit im Kelbachtal</h2>
  <div class="leisure-list">
    <article class="leisure-card">
      <div class="leisure-photo" role="img" aria-label="Angler am Fluss" style="background:linear-gradient(160deg,#7fa8c0,#4e7a5a)"></div>
      <div class="leisure-body"><h3 class="leisure-name">ANGELN</h3><p class="leisure-text">Ruhige Stunden an klaren Gewässern.</p><a class="btn" href="#">Mehr</a></div>
    </article>
    <article class="leisure-card highlight">
      <div class="leisure-photo" role="img" aria-label="Heißluftballon am Himmel" style="background:linear-gradient(180deg,#8cc3ec,#d96a4a)"></div>
      <div class="leisure-body"><h3 class="leisure-name">BALLONFAHRTEN</h3><p class="leisure-text">Das Tal von oben in aller Ruhe erleben.</p><a class="btn" href="#">Mehr</a></div>
    </article>
    <article class="leisure-card">
      <div class="leisure-photo" role="img" aria-label="Familie beim Wandern" style="background:linear-gradient(160deg,#9cc27a,#6a8a4e)"></div>
      <div class="leisure-body"><h3 class="leisure-name">WANDERWEGE</h3><p class="leisure-text">Gut beschilderte Wege für jedes Alter.</p><a class="btn" href="#">Mehr</a></div>
    </article>
    <article class="leisure-card">
      <div class="leisure-photo" role="img" aria-label="Freibad mit Liegewiese" style="background:linear-gradient(160deg,#6cc0e0,#3a8ab8)"></div>
      <div class="leisure-body"><h3 class="leisure-name">FREIBÄDER</h3><p class="leisure-text">Badeseen, Freibäder und Thermen.</p><a class="btn" href="#">Mehr</a></div>
    </article>
    <article class="leisure-card">
      <div class="leisure-photo" role="img" aria-label="Gedeckter Tisch mit regionalen Speisen" style="background:linear-gradient(160deg,#d6a86a,#9a5a3a)"></div>
      <div class="leisure-body"><h3 class="leisure-name">GASTRONOMIE</h3><p class="leisure-text">Gasthöfe, Biergärten und feine Küche.</p><a class="btn" href="#">Mehr</a></div>
    </article>
  </div>
  <div class="leisure-all"><a class="btn" href="#">Alle</a></div>
  <svg class="leisure-wave" viewBox="0 0 1200 110" preserveAspectRatio="none"><path d="M0 60 C300 0 600 120 900 50 S1150 30 1200 40 V110 H0Z" fill="#fff"/></svg>
</section>

<section class="welcome">
  <div class="welcome-text">
    <p class="welcome-kicker">Willkommen bei</p>
    <h2 class="welcome-title">Ferienverband Kelbachtal</h2>
    <p class="welcome-lead">Kelbach und Umgebung haben all das, was das Leben lebenswert macht.</p>
    <p>Kultur und Natur, Lebensfreude und Genuss, freundliche und aufgeschlossene Menschen – hier fühlen sich Gäste vom ersten Tag an wohl.</p>
    <p>Ob Kirchen, Brunnen oder historische Plätze – bei einem Rundgang durch die Kelbacher Altstadt kann man viele liebevolle Details für sich entdecken.</p>
    <p>Für Bewegungsfreudige und Erholungssuchende gibt es „mehr pur“ in und um Kelbach. Hier lassen sich sportliche Touren wunderbar mit Radeln, Walken, Wandern, Golfen, Reiten und Baden verbinden oder einfach die Ruhe genießen.</p>
    <a class="btn" href="#">Mehr lesen</a>
  </div>
  <div class="welcome-photo">
    <div class="photo" role="img" aria-label="Luftbild einer Burg über bewaldeten Hügeln"></div>
    <svg width="428" height="120" viewBox="0 0 428 120"><path d="M0 70 C120 20 260 120 428 40 V120 H0Z" fill="#1f7fc6" opacity=".85"/><path d="M0 95 C140 60 280 130 428 80 V120 H0Z" fill="#79b51c"/></svg>
  </div>
</section>

<section class="discover">
  <h2 class="section-title">Das Kelbachtal entdecken,<br>erleben und geniessen!</h2>
  <div class="town-list">
    <div class="town"><div class="town-photo" role="img" aria-label="Kirchturm von Kelbach" style="background:linear-gradient(180deg,#7ab4e4,#b9925e)"></div><p class="town-name">Kelbach</p></div>
    <div class="town"><div class="town-photo" role="img" aria-label="Landschaft bei Moosbrunn" style="background:linear-gradient(180deg,#8cbfe6,#5c8a44)"></div><p class="town-name">Moosbrunn</p></div>
    <div class="town"><div class="town-photo" role="img" aria-label="Stadttor von Haselried" style="background:linear-gradient(180deg,#6eaee6,#c0674a)"></div><p class="town-name">Haselried</p></div>
    <div class="town"><div class="town-photo" role="img" aria-label="Thermenanlage in Bad Lindau" style="background:linear-gradient(180deg,#7dc0e0,#3f8a6a)"></div><p class="town-name">Bad Lindau</p></div>
    <div class="town"><div class="town-photo" role="img" aria-label="Golfplatz bei Bad Steinach" style="background:linear-gradient(180deg,#a2cbe8,#6a9a48)"></div><p class="town-name">Bad Steinach</p></div>
    <div class="town"><div class="town-photo" role="img" aria-label="Kirche in Auwinkel" style="background:linear-gradient(180deg,#8ac0ea,#d8c8a0)"></div><p class="town-name">Auwinkel</p></div>
  </div>
</section>

<section class="directions">
  <h2 class="directions-title">So erreichen Sie uns</h2>
  <div class="map-area" role="img" aria-label="Karte der Region mit Standortmarkierungen"></div>
  <div class="video-area" role="img" aria-label="Video: Familie beim Picknick auf der Wiese">
    <svg width="60" height="60" viewBox="0 0 60 60"><circle cx="30" cy="30" r="30" fill="#fff" opacity=".92"/><path d="M24 18l18 12-18 12z" fill="#1f7fc6"/></svg>
  </div>
</section>

<footer class="site-footer" role="img" aria-label="Blick über einen Alpensee mit Dorf und Bergen">
  <svg class="footer-curve" viewBox="0 0 1200 62" preserveAspectRatio="none"><path d="M0 62 C300 0 900 0 1200 62Z" fill="#fff"/></svg>
  <div class="footer-panel"></div>
  <div class="footer-brand"><span class="brand-dot"></span><span class="brand-name">Ferienverband Kelbachtal</span></div>
  <div class="footer-cols">
    <div class="footer-col">
      <h4>FVV Kelbach</h4>
      <p>Fremdenverkehrsverein<br>Kelbach und Umgebung e.V.</p>
      <p style="margin-top:10px">Lindenweg 4, 00101 Kelbach<br>Tel.: 01234 / 555 140<br>Fax: 01234 / 555 149<br>info@wanderhof-kelbach.de</p>
    </div>
    <div class="footer-col">
      <h4>Öffnungszeiten</h4>
      <p>Mo-Fr 9:00 - 17:00 Uhr<br>Sa 9:00 - 12:00 Uhr</p>
      <p style="margin-top:10px"><a href="#">Kontakt</a><br><a href="https://www.wanderhof-kelbach.de">www.wanderhof-kelbach.de</a></p>
    </div>
    <div class="footer-col">
      <h4>Speisekarte</h4>
      <ul>
        <li>Home</li><li>Gastgeber</li><li>Kelbachtal Freizeit</li><li>Ausflugsziele</li><li>Kunst und Kultur</li><li>Kontakt</li>
      </ul>
    </div>
  </div>
  <div class="footer-bottom"><span>Veranstaltungskalender</span><span>|</span><span>Infomaterial</span><span>|</span><span>Copyright © 2025 All Rights Reserved</span></div>
</footer>

</body>
</html>
```